Kestrelway Financial Plans

I am looking for a complete resdesign of my small financial presentation. This is a Word Doc/PDF that I print off when meeting with people in private. I often present my "two pager" that I have been using for years and years. It tells them the basics of what I do, how I help people and foundational financial principles.

I have recently gone out on my own in business and have completely rebranded. This presentation is my most used tool, so it is the first of many things I would like to redo. I am hoping it will somehow coordinate with the colors of my business, not necessarily the EXACT same 3 colors everywhere, but have the design colors compliment.

I've uploaded all my logo designs, as well as the current "two-pager". I am not against it going to 3 pages if needed. As it will still land on 2 pages with duplex printing.

It has always been VERY simple. I am wanting it built into a more professional and design specific format, to show off my branding, without being over cluttered.

I am completely open to ANY graphics changes. Obviously some are very novice, the house on the last page has always been overly simplified.

```html
<!DOCTYPE html>
<html lang="en">
<head>
<meta charset="utf-8">
<title>Kestrelway Financial Plans – Two Pager</title>
<link href="https://fonts.googleapis.com/css2?family=Montserrat:wght@500;700;800&family=Manrope:wght@400;500;600;700&display=swap" rel="stylesheet">
<style>
:root{
  --green:#1f9e3a;
  --green-dark:#146c27;
  --green-soft:#e0f6e4;
  --ink:#121a2a;
  --navy:#111a2b;
  --slate:#6b737b;
  --row:#efeff0;
  --text:#2b2f36;
  --muted:#70757c;
  --white:#ffffff;
}
*{box-sizing:border-box;margin:0;padding:0}
html,body{width:1200px;height:849px;overflow:hidden}
body{
  position:relative;
  background:linear-gradient(180deg,#0f5a1e 0%,#0b3514 35%,#060a07 100%);
  font-family:"Manrope",sans-serif;color:var(--text);
}
.page{position:absolute;top:36px;width:550px;height:777px;background:var(--white);overflow:hidden}
.page-left{left:33px}
.page-right{left:619px;width:549px}
.abs{position:absolute}

.section-title{position:absolute;left:28px;font-family:"Montserrat",sans-serif;font-weight:800;font-size:18.5px;color:var(--ink);letter-spacing:.2px;white-space:nowrap;line-height:1}
.section-title em{font-style:normal;color:var(--green)}
.section-marker{position:absolute;left:0;width:0;height:0;border-top:10.5px solid transparent;border-bottom:10.5px solid transparent;border-left:22px solid var(--green)}

/* challenge cards */
.card{position:absolute;top:54px;width:146px;height:268px;border-radius:73px;background:var(--white);box-shadow:0 4px 14px rgba(31,158,58,.16);overflow:hidden}
.card-cap{position:absolute;left:0;top:0;width:146px;height:67px;border-radius:0 0 50% 50%/0 0 70% 70%;background:linear-gradient(160deg,#2aa748,#137a2a)}
.card-label{position:absolute;top:46px;width:100%;text-align:center;font-family:"Montserrat",sans-serif;font-weight:700;font-size:9px;color:var(--white);letter-spacing:.2px}
.card-icon{position:absolute;top:10px;left:61px;width:24px;height:24px;border:1.6px solid var(--white);border-radius:5px}
.card-body{position:absolute;top:75px;left:4px;right:4px;text-align:center;font-size:7.2px;line-height:14.75px;color:var(--text)}
.tick{color:var(--green);font-weight:700;margin-right:2px}

/* services */
.service{position:absolute;top:387px;width:90px;text-align:center}
.ring{margin:0 auto;width:71px;height:71px;border-radius:50%;border:11px solid var(--slate);background:var(--white);display:flex;align-items:center;justify-content:center}
.ring-icon{width:24px;height:24px;border-radius:50%;background:var(--green);color:var(--white);font-family:"Montserrat",sans-serif;font-weight:800;font-size:12px;display:flex;align-items:center;justify-content:center}
.service-label{margin-top:9px;font-family:"Montserrat",sans-serif;font-weight:500;font-size:8.4px;line-height:12px;color:var(--ink)}
.pill{position:absolute;left:28px;top:505px;width:127px;height:22px;border-radius:11px;background:var(--navy);color:var(--white);font-family:"Montserrat",sans-serif;font-weight:500;font-size:7.4px;display:flex;align-items:center;justify-content:center;box-shadow:0 0 0 1.5px var(--green)}

/* how */
.pie-label{position:absolute;width:70px;font-family:"Montserrat",sans-serif;font-weight:500;font-size:9.2px;color:var(--white);text-align:center;line-height:14px}
.savings{position:absolute;left:194px;top:669px;font-family:"Montserrat",sans-serif;font-weight:700;font-size:10.2px;color:var(--ink)}
.goal{position:absolute;left:261px;font-family:"Montserrat",sans-serif;font-weight:500;font-size:8.4px;color:var(--muted);display:flex;align-items:center;gap:6px}
.goal-ring{width:11px;height:11px;border-radius:50%;border:1.8px solid var(--muted);border-top-color:transparent;transform:rotate(-30deg)}
.partner{position:absolute;width:54px;height:22px;background:var(--green-soft);border-radius:2px;display:flex;align-items:center;justify-content:center;gap:3px;font-weight:600;font-size:5.6px;color:var(--navy);white-space:nowrap}
.partner-dot{width:5px;height:5px;border-radius:50%;background:var(--green)}
.pay-us{position:absolute;left:454px;top:757px;font-family:"Montserrat",sans-serif;font-weight:500;font-size:8.4px;color:var(--green)}

/* rule of 72 */
.rule-table{position:absolute;top:63px;width:118px;border-collapse:collapse;font-size:8.4px;box-shadow:0 0 0 1px #d9dadc}
.rule-table th{height:25px;background:var(--slate);color:var(--white);font-family:"Montserrat",sans-serif;font-weight:700;font-size:8.6px}
.rule-table td{height:26.8px;text-align:center;color:var(--ink);font-weight:500;border-right:1px solid #d6d7d9}
.rule-table td:last-child{border-right:none}
.rule-table tr:nth-child(odd) td{background:var(--row)}
.rule-table tr:nth-child(even) td{background:var(--white)}
.rule-caption{position:absolute;width:118px;text-align:center;font-weight:500;font-size:9.2px;line-height:16.5px;color:var(--green);letter-spacing:.2px}

/* taxes */
.tax-box{position:absolute;left:27px;top:401px;width:494px;height:356px;border:2px solid var(--navy);background:var(--white)}
.tax-top{position:absolute;left:0;top:0;width:100%;height:138px;background:var(--navy)}
.brand{position:absolute;top:18px;width:100%;text-align:center;color:var(--white);font-family:"Montserrat",sans-serif;font-weight:700}
.brand-name{font-size:25px;letter-spacing:1px;line-height:1}
.brand-sub{margin-top:6px;font-size:9.4px;letter-spacing:2.6px;display:flex;align-items:center;justify-content:center;gap:8px}
.brand-sub i{display:block;width:24px;height:1.5px;background:var(--white)}
.tax-cols{position:absolute;left:0;top:136px;width:100%;height:164px;display:grid;grid-template-columns:124px 121px 123px 1fr;border-bottom:3px solid var(--navy)}
.tax-col{border-left:2px solid var(--navy);text-align:center}
.tax-col:first-child{border-left:none}
.tax-head{height:29px;background:var(--green);color:var(--white);font-family:"Montserrat",sans-serif;font-weight:700;font-size:10.5px;display:flex;align-items:center;justify-content:center}
.tax-text{height:108px;padding-top:9px;font-size:9.2px;line-height:16.6px;color:var(--ink)}
.tax-result{font-family:"Montserrat",sans-serif;font-weight:700;font-size:10.5px;color:var(--green)}
.tax-foot{position:absolute;top:306px;left:0;width:100%;font-family:"Montserrat",sans-serif;font-weight:700;font-size:9.2px;color:var(--green)}
.tax-foot span{position:absolute;transform:translateX(-50%);white-space:nowrap}
.tax-rule{position:absolute;left:38px;top:20px;width:415px;height:1px;background:var(--green)}
</style>
</head>
<body>

<section class="page page-left">
  <div class="section-marker" style="top:16px"></div>
  <h2 class="section-title" style="top:17px">THE FINANCIAL <em>CHALLENGE</em></h2>

  <article class="card" style="left:27px">
    <div class="card-cap" role="img" aria-label="Photo of hands saving money with a savings icon"></div>
    <div class="card-icon" style="border-radius:50%"></div>
    <div class="card-label">SAVINGS</div>
    <p class="card-body"><span class="tick">✓</span>49% Of Canadian Employees Are<br>Living Paycheque To Paycheque. 25%<br>Of Canadians Are Unable To Cover An<br>Unexpected $500 Expense<br><span class="tick">✓</span>Statline Bureau (Feb 2023)<br>25% Of Canadians Need To Access<br>Their Retirement Savings Early. 20% Of<br>Canadians Have No Savings. 39% Of<br>Canadians Aged 55-65 Have Less<br>Than $5,000 In Savings.<br><span class="tick">✓</span>Federal Data Office<br>(June 2023)</p>
  </article>

  <article class="card" style="left:202px">
    <div class="card-cap" role="img" aria-label="Photo of a couple reviewing bills with a debt document icon"></div>
    <div class="card-icon"></div>
    <div class="card-label">DEBT</div>
    <p class="card-body"><span class="tick">✓</span>The Average Canadian Has $22,131<br>In Consumer Debt. Which Excludes<br>Mortgages.<br><span class="tick">✓</span>Creditline Bureau (Aug 2024)<br>Over 55% Of Canadians Hold Credit<br>Card Debt And The Total<br>Canadian Household Debt Has<br>Increased To $2.52trillion, Including<br>Consumer Credit, Mortgage And<br>Non-mortgage Loan</p>
  </article>

  <article class="card" style="left:376px">
    <div class="card-cap" role="img" aria-label="Photo of a family protected under an umbrella with an insurance checklist icon"></div>
    <div class="card-icon"></div>
    <div class="card-label">INSURANCE</div>
    <p class="card-body"><span class="tick">✓</span>45% Of Canadians Do Not Have<br>Individual Life Insurance Coverage, But<br>48% Say Their Families Would Face<br>Financial Trouble Within 6 Months Of<br>Losing Someone.<br><span class="tick">✓</span>Lifemark Research (Apr 2023)<br>2-in-5 Canadians (43% Women / 44%<br>Men) Will Be Diagosed With A Form Of<br>Cancer Or Other Critical Illness During<br>Their Lifetime. Every 7 Seconds.<br><span class="tick">✓</span>Wellnet Health Data<br>(June 2024)</p>
  </article>

  <div class="section-marker" style="top:349px"></div>
  <h2 class="section-title" style="top:351px">WHO ARE WE AND <em>WHAT DO WE DO?</em></h2>

  <div class="service" style="left:18px"><div class="ring"><div class="ring-icon" role="img" aria-label="Cash flow icon">$</div></div><p class="service-label">Cash Flow</p></div>
  <div class="service" style="left:100px"><div class="ring"><div class="ring-icon" role="img" aria-label="Money bag with shield icon">$</div></div><p class="service-label">Cash<br>Flow Protection</p></div>
  <div class="service" style="left:187px"><div class="ring"><div class="ring-icon" role="img" aria-label="Debt management icon">$</div></div><p class="service-label">Debt<br>Management</p></div>
  <div class="service" style="left:272px"><div class="ring"><div class="ring-icon" role="img" aria-label="Emergency fund coins icon">+</div></div><p class="service-label">Emergency<br>Fund</p></div>
  <div class="service" style="left:355px"><div class="ring"><div class="ring-icon" role="img" aria-label="Growing wealth chart icon">$</div></div><p class="service-label">Build<br>Wealth</p></div>
  <div class="service" style="left:441px"><div class="ring"><div class="ring-icon" role="img" aria-label="Hands preserving money icon">$</div></div><p class="service-label">Preserve</p></div>

  <div class="pill">EDUCATION &amp; AWARENESS</div>

  <div class="section-marker" style="top:557px"></div>
  <h2 class="section-title" style="top:559px">HOW ARE <em>WE DOING IT?</em></h2>

  <svg class="abs" style="left:0;top:600px" width="200" height="160" viewBox="0 600 200 160" aria-hidden="true">
    <circle cx="100" cy="675" r="72" fill="var(--green)"/>
    <line x1="100" y1="602" x2="100" y2="748" stroke="#fff" stroke-width="2"/>
    <line x1="100" y1="675" x2="171" y2="654" stroke="#fff" stroke-width="1.2"/>
    <line x1="100" y1="675" x2="172" y2="675" stroke="#fff" stroke-width="2"/>
    <line x1="100" y1="675" x2="169" y2="696" stroke="#fff" stroke-width="1.2"/>
  </svg>
  <div class="pie-label" style="left:27px;top:660px">Living<br>Expenses</div>
  <div class="pie-label" style="left:98px;top:643px">Taxes</div>
  <div class="pie-label" style="left:97px;top:697px">Debt</div>

  <svg class="abs" style="left:208px;top:650px" width="16" height="10" aria-hidden="true"><path d="M1 5h13M10 1l4 4-4 4" fill="none" stroke="var(--green)" stroke-width="1.2"/></svg>
  <div class="savings">SAVINGS</div>
  <svg class="abs" style="left:208px;top:686px" width="16" height="10" aria-hidden="true"><path d="M1 5h13M10 1l4 4-4 4" fill="none" stroke="var(--green)" stroke-width="1.2"/></svg>

  <div class="goal" style="top:618px"><span class="goal-ring"></span>Retirement Savings</div>
  <div class="goal" style="top:652px"><span class="goal-ring"></span>Children’s Education</div>
  <div class="goal" style="top:687px"><span class="goal-ring"></span>Proper Protection</div>
  <div class="goal" style="top:721px"><span class="goal-ring"></span>Freedom From DEPT</div>

  <svg class="abs" style="left:378px;top:671px" width="16" height="10" aria-hidden="true"><path d="M1 5h13M10 1l4 4-4 4" fill="none" stroke="var(--green)" stroke-width="1.2"/></svg>

  <div class="partner" style="left:404px;top:603px"><span class="partner-dot"></span>Maplecrest</div>
  <div class="partner" style="left:468px;top:603px">Harbourline Life</div>
  <div class="partner" style="left:404px;top:634px">Lumen Financial</div>
  <div class="partner" style="left:468px;top:634px"><span class="partner-dot"></span>Northgate Mutual</div>
  <div class="partner" style="left:404px;top:664px">Prairie Assurance</div>
  <div class="partner" style="left:468px;top:664px">Ridgeview Insurance</div>
  <div class="partner" style="left:404px;top:695px">Beacona</div>
  <div class="partner" style="left:468px;top:695px">Shoreline Insurance</div>
  <div class="partner" style="left:404px;top:725px"><span class="partner-dot"></span>Commonfield</div>
  <div class="partner" style="left:468px;top:725px">Vantra</div>

  <svg class="abs" style="left:459px;top:746px" width="10" height="10" aria-hidden="true"><path d="M5 0v9M1 5l4 4 4-4" fill="none" stroke="var(--green)" stroke-width="1"/></svg>
  <div class="pay-us">PAY US</div>
</section>

<section class="page page-right">
  <div class="section-marker" style="top:16px"></div>
  <h2 class="section-title" style="top:17px">RULE OF <em>72</em></h2>

  <table class="rule-table" style="left:27px">
    <tr><th>AGE</th><th>4%</th></tr>
    <tr><td>29</td><td>$10,000</td></tr>
    <tr><td>47</td><td>$20,000</td></tr>
    <tr><td>65</td><td>$40,000</td></tr>
  </table>
  <p class="rule-caption" style="left:27px;top:186px">MONEY DOUBLES<br>EVERY 18 YEARS</p>

  <table class="rule-table" style="left:153px">
    <tr><th>AGE</th><th>6%</th></tr>
    <tr><td>29</td><td>$10,000</td></tr>
    <tr><td>41</td><td>$20,000</td></tr>
    <tr><td>53</td><td>$40,000</td></tr>
    <tr><td>65</td><td>$80,000</td></tr>
  </table>
  <p class="rule-caption" style="left:153px;top:210px">MONEY DOUBLES<br>EVERY 12 YEARS</p>

  <table class="rule-table" style="left:278px">
    <tr><th>AGE</th><th>8%</th></tr>
    <tr><td>29</td><td>$10,000</td></tr>
    <tr><td>38</td><td>$20,000</td></tr>
    <tr><td>47</td><td>$40,000</td></tr>
    <tr><td>56</td><td>$80,000</td></tr>
    <tr><td>65</td><td>$160,000</td></tr>
  </table>
  <p class="rule-caption" style="left:278px;top:234px">MONEY DOUBLES<br>EVERY 9 YEARS</p>

  <table class="rule-table" style="left:404px">
    <tr><th>AGE</th><th>12%</th></tr>
    <tr><td>29</td><td>$10,000</td></tr>
    <tr><td>35</td><td>$20,000</td></tr>
    <tr><td>41</td><td>$40,000</td></tr>
    <tr><td>47</td><td>$80,000</td></tr>
    <tr><td>53</td><td>$160,000</td></tr>
    <tr><td>59</td><td>$320,000</td></tr>
    <tr><td>65</td><td>$640,000</td></tr>
  </table>
  <p class="rule-caption" style="left:404px;top:289px">MONEY DOUBLES<br>EVERY 6 YEARS</p>

  <div class="section-marker" style="top:360px"></div>
  <h2 class="section-title" style="top:361px">TAXES</h2>

  <div class="tax-box">
    <div class="tax-top">
      <div class="brand">
        <div class="brand-name">KESTRELWAY</div>
        <div class="brand-sub"><i></i>FINANCIAL PLANS<i></i></div>
      </div>
      <svg class="abs" style="left:0;top:78px" width="490" height="60" viewBox="0 0 490 60" aria-hidden="true">
        <polygon points="245,0 3,59 487,59" fill="var(--green)"/>
      </svg>
    </div>
    <div class="tax-cols">
      <div class="tax-col">
        <div class="tax-head">HOME</div>
        <div class="tax-text">Partner With<br>Mortgage Brokers<br>For Best Rates<br><span style="display:block;height:6px"></span>Mortgage Insurance<br>Alternatives</div>
        <div class="tax-result">SELL</div>
      </div>
      <div class="tax-col">
        <div class="tax-head">RRSP</div>
        <div class="tax-text">Tax<br>Deduction<br><br><span style="display:block;height:6px"></span>Tax<br>Deferred</div>
        <div class="tax-result">100% TAX</div>
      </div>
      <div class="tax-col">
        <div class="tax-head">TFSA</div>
        <div class="tax-text" style="line-height:22px;padding-top:4px">No Tax Deductions<br>Tax free growth<br>2009=$95,000<br>Limit 2023 - $7,000/yr</div>
        <div class="tax-result">0% TAX</div>
      </div>
      <div class="tax-col">
        <div class="tax-head">PERM LIFE</div>
        <div class="tax-text" style="line-height:22px;padding-top:4px">No Tax Deductions<br>Qualify<br>Tax Deferred<br>Growth</div>
        <div class="tax-result">0% TAX</div>
      </div>
    </div>
    <div class="tax-foot">
      <span style="left:112px;top:0">Life Insurance Illness</span>
      <span style="left:369px;top:0">Debt Management</span>
      <div class="tax-rule"></div>
      <span style="left:112px;top:21px">Critical/disability</span>
      <span style="left:369px;top:21px">Cash Flow</span>
    </div>
  </div>
</section>

</body>
</html>
```